Local fast-growing company in the service sector

We are looking for a modern business card design, which should also appear on our letterheads

Target Market(s)

Private and industrial sectors

Contact Information for Business Card

Vorname Name
Kellberger Str. 18
73614 Lindenfeld
Tel.: 07146-839214-0
Name@agentur-kvtl.de

Colors
9d9d9d
919191
aaaaaa

Requirements
Must have
• The logo (file) in silver

```html
<!DOCTYPE html>
<html lang="de">
<head>
<meta charset="UTF-8">
<title>KVTL Visitenkarte</title>
<link href="https://fonts.googleapis.com/css2?family=Roboto:wght@300;400;500&display=swap" rel="stylesheet">
<style>
  :root {
    --bg: #ececec;
    --frame: #6f6f6f;
    --panel: #ffffff;
    --ink: #1c1c1c;
    --silver: #9d9d9d;
    --silver-mid: #919191;
    --silver-light: #aaaaaa;
    --rule: #5a5a5a;
  }
  html, body {
    margin: 0;
    padding: 0;
    width: 1200px;
    height: 1200px;
    overflow: hidden;
    background: var(--bg);
    font-family: "Roboto", Arial, sans-serif;
  }
  .business-card {
    position: absolute;
    left: 100px;
    top: 280px;
    width: 1000px;
    height: 640px;
    box-shadow: 0 10px 30px rgba(0,0,0,0.18);
  }
  .card-frame {
    position: absolute;
    inset: 0;
    display: block;
  }
  .brand {
    position: absolute;
    left: 90px;
    top: 285px;
    display: flex;
    align-items: center;
    gap: 18px;
  }
  .brand-square {
    width: 54px;
    height: 54px;
    background: var(--silver);
  }
  .brand-name {
    font-size: 64px;
    font-weight: 500;
    color: var(--silver);
    letter-spacing: 2px;
    line-height: 1;
  }
  .contact {
    position: absolute;
    left: 480px;
    top: 200px;
    width: 460px;
    color: var(--ink);
  }
  .contact p { margin: 0; }
  .person {
    font-size: 40px;
    font-weight: 400;
    white-space: nowrap;
    padding: 0 0 14px 20px;
    line-height: 1.1;
  }
  .person .position {
    font-size: 20px;
    font-weight: 300;
    color: var(--silver-light);
  }
  .rule {
    height: 1.5px;
    background: var(--rule);
  }
  .address {
    font-size: 22px;
    padding: 16px 0 22px 20px;
    white-space: nowrap;
  }
  .phone-row {
    display: flex;
    justify-content: space-between;
    align-items: baseline;
    padding: 18px 0 8px 20px;
  }
  .phone {
    font-size: 24px;
    white-space: nowrap;
  }
  .web {
    font-size: 20px;
    color: var(--ink);
    white-space: nowrap;
  }
  .email {
    font-size: 24px;
    color: var(--silver-light);
    padding-left: 20px;
  }
</style>
</head>
<body>
  <div class="business-card">
    <svg class="card-frame" width="1000" height="640" viewBox="0 0 1000 640" aria-hidden="true">
      <rect x="0" y="0" width="1000" height="640" fill="var(--frame)"/>
      <rect x="14" y="14" width="972" height="612" fill="none" stroke="#ffffff" stroke-width="2"/>
      <path d="M76,34 H924 A42,42 0 0 0 966,76 V564 A42,42 0 0 0 924,606 H76 A42,42 0 0 0 34,564 V76 A42,42 0 0 0 76,34 Z"
            fill="none" stroke="#ffffff" stroke-width="2"/>
      <path d="M80,42 H920 A38,38 0 0 0 958,80 V560 A38,38 0 0 0 920,598 H80 A38,38 0 0 0 42,560 V80 A38,38 0 0 0 80,42 Z"
            fill="var(--panel)"/>
    </svg>

    <div class="brand">
      <span class="brand-square"></span>
      <span class="brand-name">KVTL</span>
    </div>

    <div class="contact">
      <p class="person">Vorname Name <span class="position">| Position</span></p>
      <div class="rule"></div>
      <p class="address">Kellberger Str. 18, 73614 Lindenfeld</p>
      <div class="rule"></div>
      <div class="phone-row">
        <p class="phone">Phone 07146-839214-0</p>
        <span class="web">agentur-kvtl.de</span>
      </div>
      <p class="email">Name@agentur-kvtl.de</p>
    </div>
  </div>
</body>
</html>
```